Need Business Card for our Real Estate Business with Sales Executive's Picture

PANTONE 484 C ( RED)

PANTONE 2766 C ( BLUE

Industry/Entity Type

Real Estate

Contact Information for Business Card

Name, Mobile, email, & picture of Person
Agency Phone, address, Web address

Requirements
Must have
• Our Logo Colours, Agent Picture,

```html
<!DOCTYPE html>
<html lang="en">
<head>
<meta charset="utf-8">
<title>Dunmore Realty Business Card</title>
<link rel="stylesheet" href="https://fonts.googleapis.com/css2?family=Open+Sans:wght@400;600&display=swap">
<style>
  :root {
    --page-bg: #5a5a5c;
    --card-bg: #2a2a2c;
    --brand-red: #c0282d;
    --brand-blue: #1c3474;
    --text-light: #f2f2f2;
    --portrait-top: #4a4d55;
    --portrait-bottom: #33353b;
  }
  * { margin: 0; padding: 0; box-sizing: border-box; }
  html, body {
    width: 799px; height: 1200px; overflow: hidden;
    background: var(--page-bg);
    font-family: "Open Sans", Arial, sans-serif;
  }
  .canvas {
    position: relative; width: 799px; height: 1200px;
    display: flex; flex-direction: column; align-items: center; justify-content: center; gap: 110px;
  }
  .card {
    position: relative; width: 660px; height: 377px;
    background: var(--card-bg);
    box-shadow: 0 14px 30px rgba(0,0,0,.35);
    overflow: hidden;
  }
  /* Front side */
  .front-brand {
    position: absolute; left: 0; right: 0; top: 130px;
    display: flex; align-items: center; justify-content: center; gap: 14px;
  }
  .front-brand .brand-square { width: 22px; height: 22px; background: #3c3c3f; }
  .front-brand .brand-name { font-size: 34px; font-weight: 600; color: #4a4a4e; letter-spacing: .5px; }
  .front-web {
    position: absolute; left: 0; right: 0; bottom: 64px;
    display: flex; align-items: center; justify-content: center; gap: 18px;
    color: var(--text-light); font-size: 17px; letter-spacing: .3px;
  }
  .front-web .rule { width: 70px; height: 3px; background: var(--brand-red); }

  /* Back side */
  .back-band { position: absolute; inset: 0; width: 660px; height: 377px; }
  .agent { position: absolute; left: 40px; top: 40px; }
  .agent-name { color: var(--brand-red); font-size: 22px; font-weight: 600; }
  .agent-title { color: var(--text-light); font-size: 14px; margin-top: 2px; }
  .agent-portrait {
    position: absolute; right: 40px; top: 36px; width: 104px; height: 124px;
    background: linear-gradient(180deg, var(--portrait-top), var(--portrait-bottom));
    border: 2px solid var(--brand-blue);
  }
  .contact { position: absolute; left: 40px; top: 140px; color: var(--text-light); font-size: 15.5px; line-height: 1.5; }
  .contact .address { margin-bottom: 8px; }
  .contact-row { display: flex; align-items: center; gap: 10px; }
  .contact-row svg { width: 13px; height: 13px; flex: none; fill: var(--brand-red); }
  .contact-row .accent { color: var(--brand-red); }
  .back-brand {
    position: absolute; right: 40px; top: 200px;
    display: flex; align-items: center; gap: 12px;
  }
  .back-brand .brand-square { width: 34px; height: 34px; background: var(--brand-red); }
  .back-brand .brand-name { font-size: 26px; font-weight: 600; color: var(--text-light); }
</style>
</head>
<body>
<main class="canvas">
  <section class="card card-front" aria-label="Card front">
    <div class="front-brand">
      <span class="brand-square"></span>
      <span class="brand-name">Dunmore Realty</span>
    </div>
    <div class="front-web">
      <span class="rule"></span>
      <span>www.dunmorerealty.com</span>
      <span class="rule"></span>
    </div>
  </section>

  <section class="card card-back" aria-label="Card back">
    <svg class="back-band" viewBox="0 0 660 377" aria-hidden="true">
      <polygon points="0,296 0,312 380,377 430,377" fill="#1c3474"/>
      <polygon points="660,250 660,377 470,377" fill="#1c3474"/>
    </svg>
    <div class="agent">
      <div class="agent-name">Marianne Hollis</div>
      <div class="agent-title">Managing Director</div>
    </div>
    <div class="agent-portrait" role="img" aria-label="Portrait photo of the sales executive"></div>
    <div class="contact">
      <div class="address">418 Cedar Ridge Ave #210,<br>Fairview, CO 80412</div>
      <div class="contact-row">
        <svg viewBox="0 0 16 16"><path d="M3 1h3l1.5 4-2 1.3a9 9 0 0 0 4.2 4.2L11 8.5l4 1.5v3a2 2 0 0 1-2 2A13 13 0 0 1 1 3a2 2 0 0 1 2-2z"/></svg>
        <span>555.210.4836</span>
      </div>
      <div class="contact-row">
        <svg viewBox="0 0 16 16"><path d="M3 1h3l1.5 4-2 1.3a9 9 0 0 0 4.2 4.2L11 8.5l4 1.5v3a2 2 0 0 1-2 2A13 13 0 0 1 1 3a2 2 0 0 1 2-2z"/></svg>
        <span>555-318-2749</span>
      </div>
      <div class="contact-row">
        <svg viewBox="0 0 16 16"><path d="M1 3h14v10H1z M1 3l7 6 7-6" fill="none" stroke="#c0282d" stroke-width="1.8"/></svg>
        <span>mhollis@dunmorerealty.com</span>
      </div>
      <div class="contact-row">
        <svg viewBox="0 0 16 16"><circle cx="8" cy="8" r="6.5" fill="none" stroke="#c0282d" stroke-width="1.8"/><path d="M1.5 8h13M8 1.5c-3 3.5-3 9.5 0 13M8 1.5c3 3.5 3 9.5 0 13" fill="none" stroke="#c0282d" stroke-width="1.2"/></svg>
        <span>www.<span class="accent">dunmorerealty</span>.com</span>
      </div>
    </div>
    <div class="back-brand">
      <span class="brand-square"></span>
      <span class="brand-name">Dunmore Realty</span>
    </div>
  </section>
</main>
</body>
</html>
```